Tidewell Horizon Magazine need Logo desing and front page for 1 edittion

This is a new magazine that will be circulating in Panama. the magazine will run non for profit,will be mostly informative and few advertizers to cover printing costs.
the magaine will oncce every 2 or 3 month. we need to present it to the editors who will be aproving or diss aproving the project.

we need a Logo desing for the name of the magazine "Tidewell Horizon" and the "front cover desing for the first edition" it will be good if the designer can incude the designed format for the iner magazine, for us just to add in the artucles and the spaces for advertizing.

the magazine content will be articles by govenment energy sectors, gloval warming articles, articles in renewvable enery, university profesor talking or promoting new ideas or university advances, orientations, special edition on book or international articles about the subject on saving enerty, different sectors, world innovations in renewbable energy, and the companies who will advertize will be comapnies selling VORN products, companies offfering product and services on renewvable energy, Led product and systems companies etc...

Printing

```html
<!DOCTYPE html>
<html lang="en">
<head>
<meta charset="utf-8">
<title>Tidewell Horizon — Going green spread</title>
<link href="https://fonts.googleapis.com/css2?family=Bodoni+Moda:opsz,wght@6..96,400;6..96,500&family=Jost:ital,wght@0,300;0,400;1,300;1,400&display=swap" rel="stylesheet">
<style>
  :root {
    --green: #2ba84a;
    --blue-band: #1a8cc4;
    --ink: #2a2a2a;
    --paper: #ffffff;
    --sky-top: #5f9fd6;
    --sky-mid: #a9cdec;
    --grass: #9cc94a;
    --grass-light: #d8e98a;
  }
  * { margin: 0; padding: 0; box-sizing: border-box; }
  html, body { width: 1200px; height: 776px; overflow: hidden; background: var(--paper); }
  .spread { position: relative; width: 1200px; height: 776px; font-family: "Jost", sans-serif; color: var(--ink); }

  .page-left { position: absolute; left: 0; top: 0; width: 600px; height: 776px; background: var(--paper); overflow: hidden; }
  .section-band {
    position: absolute; left: 28px; top: 28px; width: 544px; height: 22px;
    background: var(--blue-band); color: #fff;
    font-family: "Bodoni Moda", serif; font-size: 17px; line-height: 22px; padding-left: 4px;
  }
  .headline {
    position: absolute; left: 28px; top: 124px;
    font-family: "Bodoni Moda", serif; font-weight: 500; font-size: 100px; line-height: 1;
    color: var(--green); letter-spacing: -1px; white-space: nowrap;
    transform: scaleX(0.86); transform-origin: left top;
  }
  .subhead {
    position: absolute; right: 28px; top: 226px;
    font-family: "Jost", sans-serif; font-style: italic; font-weight: 400; font-size: 24px; color: #1a1a1a;
  }
  .column {
    position: absolute; top: 276px; width: 262px;
    font-size: 12.3px; line-height: 16.6px; text-align: justify; font-weight: 400;
    hyphens: auto; -webkit-hyphens: auto;
  }
  .column p { margin: 0; }
  .column-one { left: 28px; }
  .column-two { left: 310px; }
  .drop-cap {
    float: left; font-family: "Jost", sans-serif; font-weight: 300;
    font-size: 62px; line-height: 52px; margin: 2px 5px 0 -2px;
  }
  .column h2 {
    font-family: "Bodoni Moda", serif; font-weight: 500; font-size: 17px; color: var(--green);
    line-height: 20px; margin: 13px 0 1px; text-align: left;
  }
  .opinion-box {
    position: absolute; left: 310px; top: 603px; width: 262px; height: 131px;
    background: var(--green); border-radius: 10px; color: #fff; padding: 9px 9px;
  }
  .opinion-box h3 { font-family: "Bodoni Moda", serif; font-weight: 500; font-size: 18px; line-height: 22px; margin-bottom: 4px; }
  .opinion-box p { font-style: italic; font-size: 12px; line-height: 17px; hyphens: auto; -webkit-hyphens: auto; }

  .folio { position: absolute; top: 746px; font-family: "Bodoni Moda", serif; font-size: 13px; font-weight: 500; color: #1a1a1a; }
  .masthead-mark { position: absolute; top: 746px; font-family: "Bodoni Moda", serif; font-size: 12px; font-weight: 500; color: var(--green); }

  .page-right { position: absolute; left: 600px; top: 0; width: 600px; height: 776px; overflow: hidden; }
  .cover-photo {
    position: absolute; inset: 0;
    background: linear-gradient(180deg, var(--sky-top) 0%, var(--sky-mid) 35%, #8fb8dc 62%, #c9dff0 76%, var(--grass-light) 84%, var(--grass) 100%);
  }
  .key-message {
    position: absolute; left: 32px; top: 604px; width: 560px;
    font-family: "Jost", sans-serif; font-style: italic; font-weight: 300;
    font-size: 58px; line-height: 66px; color: #1e1e1e; letter-spacing: 1px; white-space: nowrap;
  }
</style>
</head>
<body>
<div class="spread">
  <section class="page-left">
    <div class="section-band">Green Features</div>
    <h1 class="headline">Going green</h1>
    <div class="subhead">What does it mean?</div>

    <div class="column column-one">
      <p><span class="drop-cap">R</span>o hi, obus sesid confex sena nonstum nonsultorio, taliciam, quium incepesNon tem verissu libusa re muscem iumus, et;To elicaet? Risquam tereis. Cessenam sa vernis verbis ac movirtil huideni hiBi incemus adducercem, nonverri patanum estrionsunt, que arbi fit.</p>
      <p>Tor untiu voc mius et ventus, ficte, que prox manteret iliamquit; ne forteli, nostraedees vis, utus for adela manum adhum iam nostreb efaceris, ut verfex nos viconum nonsulegili iaequam crissus ceme di pris. Robut acchuid erfirib utebatiam sens se, trarter estrice lissidi pra vestracta vastis. Valabulvili, Cat.</p>
      <h2>The multiple meanings</h2>
      <p>Si iaequa reviliculus cris. Ad mum cae clego avo, morte, Paliamed con andientiliam usquonf ecurorae ne confina tustre, te non hos in peris dem dum tuam nicultus, cae nosta vividelatrum con vero cae iam perce eorteris. Graet ia deffrem arei im noximussa rescrum porum consusq uamendit quod nostemus. Aximus liissi fachucta, senimortiam tes vivatus vis ego condie prorae eo, nonlocur hae cae cre, menducipte pritimus ma, stis. intem ce teriusquem et quam iaetri sendiis publis cupio, efacrum urnimilis, Cati, prest? quem hoste</p>
    </div>

    <div class="column column-two">
      <p>cenatum aut ad nim cuppl. Senem porbem re publint iliciam poentum ponim acrebatuit, quamqua mquitar istraes es Mar</p>
      <p>Ximedii considiu consiss umumus, Castide liconsula duconihicam hus</p>
      <h2>The multiple solutions</h2>
      <p>publiae convere contere ssedo, cone alestia noca aderobus in ac mo aude ad co ut finam publis. Do, quit? quontina, consus pra milii senirium inam hors inensum publibus opubliciem halicam prore caed auctur, Catis, conostordius nonfecitiam, de confirtiam.</p>
      <p>Rae inatebatum lostem aut factum ori se fex moltum nostimus ilibus henatus iam ego publicae iam perce eorteris. Graet ia deffrem arei fur hillari pionsup ientebus bonum, tississulius macii etodit pratimurs M. Vala pos ne mena, quo nostis; nocrum untem haberius, potique.</p>
    </div>

    <aside class="opinion-box">
      <h3>Your opinion matters to us</h3>
      <p>De es, fordiem overic tus, que aperess erimus iam nonsula vit, con aceste nes, quo C. Go me cum incepon iuspio et, inatum inatilles vius nortum ad des habem se desimpostem untrudemus se confecto una.</p>
    </aside>

    <span class="folio" style="left:28px;">6</span>
    <span class="masthead-mark" style="left:470px;">Tidewell Horizon</span>
  </section>

  <section class="page-right">
    <div class="cover-photo" role="img" aria-label="Photo of a blue eye blended into a cloudy sky above a green meadow"></div>
    <p class="key-message">Important message<br>goes right over here.</p>
    <span class="masthead-mark" style="left:28px;">Tidewell Horizon</span>
    <span class="folio" style="left:584px;">7</span>
  </section>
</div>
</body>
</html>
```